Design the Business card for NetVaultic

Business card required for a professional Cyber Security business.
Company Logo and Icon has already been provided however I would like other options for the logo and icon to compare to. Alternatively, please refine/enhance the image of the logo.icon I have already provided.

If you are going to use the provided logo and icon, I was thinking that the company raised Logo on White background would serve well on the front of the card. See attached. AND, a large company raised stand-alone icon to appear on black background on the back of the card with tagline 'Cyber Risk Management, Governance and Consulting' or 'Cyber Security for your Business' See attached.
Alternatively, provide your own design for the logo and icon.

Target Market(s)

Enterprise, Government, Financial.

Contact Information for Business Card

Tavin Orloweth
Founder and CEO

Email Address
Mobile Number
Website URL
LinkedIn URL

Logo Text

NetVaultic - see attached example of logo

Font styles to use
Other font styles liked:
• Berlin Sans FB

Requirements
Must have
• Clean large and bold icon on the back with tagline.
• Horizontal alignment,
Nice to have
• Round edges.
• Raised Logo/Icon
Should not have
• An unprofessional look and feel.

```html
<!DOCTYPE html>
<html lang="en">
<head>
<meta charset="utf-8">
<title>NetVaultic Business Card</title>
<link rel="stylesheet" href="https://fonts.googleapis.com/css2?family=Varela+Round&family=Roboto:wght@400;700&display=swap">
<style>
  :root {
    --stage: #2b2b2d;
    --brand-blue: #0b72c2;
    --card-white: #f3f3f3;
    --accent-yellow: #f5c400;
    --text-white: #ffffff;
    --back-dark: #1b1c1e;
    --tag-blue: #4a6fcf;
    --tag-yellow: #f5c010;
  }
  * { margin: 0; padding: 0; box-sizing: border-box; }
  html, body { width: 1200px; height: 960px; overflow: hidden; }
  body { background: var(--stage); position: relative; font-family: "Roboto", Arial, sans-serif; }

  .card { position: absolute; width: 600px; height: 342px; overflow: hidden; }
  .card-front { left: 314px; top: 113px; background: var(--card-white); }
  .card-back { left: 311px; top: 473px; background: var(--back-dark); }

  .front-band { position: absolute; inset: 0; }

  .connector-art {
    position: absolute; left: 166px; top: 0; width: 316px; height: 342px;
    background: linear-gradient(100deg, var(--brand-blue) 0%, var(--brand-blue) 35%, #9cc3e3 62%, var(--card-white) 100%);
  }

  .holder { position: absolute; left: 35px; top: 34px; color: var(--text-white); }
  .holder-name { font-family: "Varela Round", Arial, sans-serif; font-weight: 700; font-size: 20px; color: var(--accent-yellow); line-height: 1.1; }
  .holder-title { font-family: "Varela Round", Arial, sans-serif; font-weight: 700; font-size: 14px; margin-top: 3px; }

  .contact-list { list-style: none; margin-top: 18px; }
  .contact-item { display: flex; align-items: center; font-size: 14px; height: 19px; }
  .contact-icon { width: 14px; height: 14px; margin-right: 9px; flex: none; }

  .front-brand { position: absolute; left: 310px; top: 210px; display: flex; align-items: center; }
  .brand-dot { width: 50px; height: 50px; border-radius: 50%; background: var(--brand-blue); margin-right: 8px; }
  .brand-name { font-family: "Varela Round", Arial, sans-serif; font-size: 33px; color: var(--brand-blue); line-height: 1; }

  .back-mark { position: absolute; left: 50%; top: 62px; transform: translateX(-50%); display: flex; flex-direction: column; align-items: center; }
  .back-dot { width: 120px; height: 120px; border-radius: 50%; background: var(--tag-blue); }
  .back-name { font-family: "Varela Round", Arial, sans-serif; font-size: 26px; color: var(--tag-blue); margin-top: 14px; line-height: 1; }
  .tagline { position: absolute; left: 0; right: 0; top: 277px; text-align: center; font-family: "Varela Round", Arial, sans-serif; font-weight: 700; font-size: 18px; }
  .tagline-blue { color: var(--tag-blue); }
  .tagline-yellow { color: var(--tag-yellow); }
</style>
</head>
<body>
  <section class="card card-front">
    <svg class="front-band" width="600" height="342" viewBox="0 0 600 342" aria-hidden="true">
      <path d="M0,0 H398 C300,40 212,150 204,342 H0 Z" fill="var(--brand-blue)"/>
    </svg>
    <div class="connector-art" role="img" aria-label="Decorative curved cable with round connector ends"></div>

    <div class="holder">
      <h1 class="holder-name">Tavin Orloweth</h1>
      <p class="holder-title">Founder &amp; CEO</p>
      <ul class="contact-list">
        <li class="contact-item">
          <svg class="contact-icon" viewBox="0 0 14 14"><rect x="3.5" y="0.5" width="7" height="13" rx="1.5" fill="var(--accent-yellow)"/><rect x="5" y="2.5" width="4" height="8" fill="var(--brand-blue)"/></svg>
          555 014 2290
        </li>
        <li class="contact-item">
          <svg class="contact-icon" viewBox="0 0 14 14"><rect x="1" y="3" width="12" height="8" fill="var(--accent-yellow)"/><path d="M1,3 L7,8 L13,3" fill="none" stroke="var(--brand-blue)" stroke-width="1.2"/></svg>
          tavin@netvaultic.com
        </li>
        <li class="contact-item">
          <svg class="contact-icon" viewBox="0 0 14 14"><circle cx="7" cy="7" r="6" fill="var(--accent-yellow)"/><path d="M1,7 H13 M7,1 C4,4 4,10 7,13 M7,1 C10,4 10,10 7,13" fill="none" stroke="var(--brand-blue)" stroke-width="1"/></svg>
          www.netvaultic.com
        </li>
        <li class="contact-item">
          <svg class="contact-icon" viewBox="0 0 14 14"><circle cx="7" cy="7" r="6" fill="var(--accent-yellow)"/></svg>
          netvaultic
        </li>
      </ul>
    </div>

    <div class="front-brand">
      <span class="brand-dot"></span>
      <span class="brand-name">NetVaultic</span>
    </div>
  </section>

  <section class="card card-back">
    <div class="back-mark">
      <span class="back-dot"></span>
      <span class="back-name">NetVaultic</span>
    </div>
    <p class="tagline"><span class="tagline-blue">Cyber Risk Management,</span> <span class="tagline-yellow">Governance &amp; Consulting</span></p>
  </section>
</body>
</html>
```